Moxy Fen needs some awesome stationary

Do you have what it takes to get my brand? You either do or you don't, have a crack at a design and you my just win my business.

I don't want to waste your or my time, so put your creative genius on either a business card or envelope.

I however need a package of stationary that follows the same brand. I will message you to complete the remaining should I like your first submission.

Here is what I need, have a go!

Basically I need the following for my small business based in melbourne.
- Letterhead (printer ready and MS Word)
- Business Card
- Compliments Slip
- Envelope
- Proposal Cover Page (MS Word only)
- Presentation Folder
- Marbled Fox Cards
- Student Name Tent
- Index Cards
- Vell-Ka

I am establishing the brand and it must be modern, professional but also relaxed; that is not formal and not corporate. It represents a company are leaders, but small enough to care and operate like a bunch of friends. We are bringing people and conversations back to business, and turfing out all the bureaucracy and crazy and wasteful procedures. Its about "lets talk and figure it out together and find even better ways".

Target Market(s)

Mainly companies that build software products, but Agile practices are used in many other industries (even graphic design projects)

Industry/Entity Type

Information Technology

Font styles to use
Sans Serif

Colors
3176b5
aaaaaa

Requirements
Must have
• I like curves and circles and not boxes or rectangles.
• I want a colour rich design with my brand colours, but it must be balanced.
• I want more modern than traditional, but simple modern
Should not have
• Not corporate
• Please don't waste my time if your not going to think about it.
• Don't mess with my primary logo
• Don't change my colours
• Don't overlay logo on image

```html
<!DOCTYPE html>
<html lang="en">
<head>
<meta charset="utf-8">
<title>Moxy Fen – Business Card</title>
<link href="https://fonts.googleapis.com/css2?family=Open+Sans:wght@400;600;700&display=swap" rel="stylesheet">
<style>
  :root {
    --brand-blue: #2c56a2;
    --brand-blue-deep: #234a8f;
    --brand-blue-light: #3a66b3;
    --brand-grey: #9ea3ab;
    --text-grey: #8a8f97;
    --panel: #eef0f3;
    --white: #ffffff;
    --backdrop: #e9e9ea;
  }
  * { margin: 0; padding: 0; box-sizing: border-box; }
  html, body {
    width: 1200px; height: 800px; overflow: hidden;
    background: var(--backdrop);
    font-family: "Open Sans", Arial, sans-serif;
  }
  .stage { position: relative; width: 1200px; height: 800px; }

  .card {
    position: absolute; top: 248px;
    width: 428px; height: 279px;
    overflow: hidden;
    background: var(--brand-blue);
  }
  .card--front { left: 114px; }
  .card--back { left: 651px; }

  /* Front */
  .holder { position: absolute; left: 25px; top: 62px; color: var(--white); }
  .holder__name { font-size: 18px; font-weight: 700; letter-spacing: 0.2px; }
  .holder__role { font-size: 10px; font-weight: 600; margin-top: 2px; }

  .contact { position: absolute; left: 25px; top: 123px; list-style: none; color: var(--white); font-size: 12.5px; line-height: 18px; }
  .contact__item { display: flex; align-items: flex-start; margin-bottom: 2px; }
  .contact__icon { width: 12px; height: 12px; margin: 3px 10px 0 0; flex: none; }

  .panel {
    position: absolute; left: 227px; top: 19px;
    width: 201px; height: 245px;
    background: var(--panel);
    border-top-left-radius: 40px;
    text-align: center;
  }
  .brand-mark { display: block; margin: 44px auto 0; width: 48px; height: 48px; border-radius: 50%; background: var(--brand-blue); }
  .brand-name { margin-top: 8px; font-size: 29px; font-weight: 600; color: var(--brand-blue); line-height: 1.1; }
  .company { margin-top: 34px; font-size: 11.5px; line-height: 17.5px; color: var(--text-grey); }
  .company__legal { font-weight: 700; }
  .company strong { font-weight: 700; }

  .edge-bar { position: absolute; left: 0; bottom: 0; width: 320px; height: 15px; background: var(--brand-grey); }

  /* Back */
  .back-field {
    position: absolute; inset: 0;
    background: radial-gradient(circle at 50% 50%, var(--brand-blue-light) 0%, var(--brand-blue) 55%, var(--brand-blue-deep) 100%);
  }
  .back-brand {
    position: absolute; left: 0; right: 0; top: 116px;
    display: flex; justify-content: center; align-items: center; gap: 12px;
  }
  .back-brand__mark { width: 36px; height: 36px; border-radius: 50%; background: var(--white); }
  .back-brand__name { font-size: 36px; font-weight: 600; color: var(--white); line-height: 1; }
  .back-url { position: absolute; left: 0; right: 0; top: 172px; text-align: center; color: var(--white); font-size: 16px; }
</style>
</head>
<body>
<main class="stage">

  <section class="card card--front" aria-label="Business card front">
    <div class="holder">
      <h1 class="holder__name">Dane Corvell</h1>
      <p class="holder__role">CEO, Professional Agile Coach</p>
    </div>

    <ul class="contact">
      <li class="contact__item">
        <svg class="contact__icon" viewBox="0 0 12 12" aria-hidden="true"><path d="M6 0.5a4 4 0 0 0-4 4c0 3 4 7 4 7s4-4 4-7a4 4 0 0 0-4-4zm0 5.5a1.5 1.5 0 1 1 0-3 1.5 1.5 0 0 1 0 3z" fill="#fff"/></svg>
        <span>PO Box 4417, Ashvale<br>North, VIC 3190, Australia</span>
      </li>
      <li class="contact__item">
        <svg class="contact__icon" viewBox="0 0 12 12" aria-hidden="true"><rect x="0.8" y="2" width="10.4" height="8" rx="1" fill="none" stroke="#fff" stroke-width="1.2"/><path d="M1 2.6l5 4 5-4" fill="none" stroke="#fff" stroke-width="1.2"/></svg>
        <span>dane@moxy-fen.com.au</span>
      </li>
      <li class="contact__item">
        <svg class="contact__icon" viewBox="0 0 12 12" aria-hidden="true"><path d="M2.6 0.8l2 2.4-1.1 1.4c0.7 1.6 2 2.9 3.6 3.6l1.4-1.1 2.4 2-1 2c-4.8 0-8.9-4.1-8.9-8.9z" fill="#fff"/></svg>
        <span>+61 400 123 987</span>
      </li>
    </ul>

    <div class="panel">
      <span class="brand-mark" aria-hidden="true"></span>
      <p class="brand-name">Moxy Fen</p>
      <p class="company">
        <span class="company__legal">Moxy Fen Pty Ltd</span><br>
        Phone <strong>1300MOXYF</strong><br>
        www.moxy-fen.com.au
      </p>
    </div>

    <div class="edge-bar"></div>
  </section>

  <section class="card card--back" aria-label="Business card back">
    <div class="back-field" role="img" aria-label="Radiating dot pattern in brand blue"></div>
    <div class="back-brand">
      <span class="back-brand__mark" aria-hidden="true"></span>
      <span class="back-brand__name">Moxy Fen</span>
    </div>
    <p class="back-url">www.moxy-fen.com.au</p>
  </section>

</main>
</body>
</html>
```